Web Design Project for SEARCH ENGINE !

We need a website design for torrents search engine.

The Website will be www.Qentrova.com

Qentrova is a a search engine for torrents.
Qentrova search and index torrents results from all torrents sites.

We will need:
Logo
WebSite Design
slogen (optional)

we need only PSDs - no codded pages are needed !

Design to the following screen Size & resolution: 1024 x 768

***PLEASE DOWNLOAD ATTACHED FILE !

```html
<!DOCTYPE html>
<html lang="en">
<head>
<meta charset="utf-8">
<title>Qentrova – Torrents Search Engine</title>
<link href="https://fonts.googleapis.com/css2?family=Source+Sans+3:wght@400;600;700&family=Arimo:wght@400&display=swap" rel="stylesheet">
<style>
:root{
  --ink:#1e1e1e;
  --bar-top:#3a3a3a;
  --bar-bottom:#151515;
  --green:#2dab3c;
  --green-bright:#39c24a;
  --red:#d0202a;
  --orange:#f08a1c;
  --blue:#1aa3dc;
  --seed:#4fba3c;
  --grey-band:#d2d2d2;
  --grey-panel:#e9e9e9;
  --grey-field:#e6e6e6;
  --text:#3a3a3a;
  --muted:#8a8a8a;
  --rule:#bdbdbd;
  --white:#fff;
}
*{box-sizing:border-box;margin:0;padding:0}
html,body{width:989px;height:1200px;overflow:hidden}
body{font-family:"Source Sans 3",sans-serif;color:var(--text);background:linear-gradient(#fff 0,#fff 900px,#ececec 1200px);position:relative}
.abs{position:absolute}

.social{top:26px;display:flex;gap:17px}
.social span{width:18px;height:18px;border-radius:3px;display:block}
.social.left{left:10px}
.social.right{left:841px}
.s1{background:#3b5a9a}.s2{background:#5bb8e0}.s3{background:#f29a2e}.s4{background:#3b6fb0}
.s5{background:#4a4a4a}.s6{background:#d9d9d9}.s7{background:#7aa83a}.s8{background:#c8302c}

.brand{left:18px;top:72px;width:122px}
.brand-name{display:flex;align-items:center;gap:3px;font-weight:700;font-size:22px;color:var(--green);line-height:1;white-space:nowrap}
.brand-name i{width:19px;height:19px;border-radius:50%;background:var(--green);display:block;flex:none}
.brand-tag{font-size:9px;color:#555;margin-top:4px;white-space:nowrap}

.topnav{left:147px;top:0;width:684px;height:56px;background:linear-gradient(var(--bar-top),var(--bar-bottom));border-radius:0 0 8px 8px;display:flex;align-items:center;padding-left:15px}
.topnav a{color:var(--white);text-decoration:none;font-size:14.5px}
.topnav a.active{color:var(--green-bright)}
.topnav .sep{color:#fff;margin:0 7px;font-size:14px}
.lang{position:absolute;right:15px;top:19px;width:66px;height:21px;background:var(--green);color:#fff;font-size:11.5px;padding:3px 0 0 8px}
.lang::after{content:"";position:absolute;right:8px;top:8px;border:4px solid transparent;border-top:6px solid #fff}

.searchbar{left:147px;top:78px;width:683px;height:31px;background:var(--grey-field);display:flex;justify-content:space-between}
.searchbar .query{font-size:18px;padding:4px 7px;color:#444}
.searchbar .go{width:62px;background:var(--ink);color:#fff;font-size:10px;display:flex;align-items:center;justify-content:center;gap:3px}
.stats{left:147px;top:113px;font-size:10.5px}
.include{left:728px;top:113px;font-size:10.5px;display:flex;gap:3px;align-items:center}
.include b{width:10px;height:10px;border:1px solid #555;display:block}

.pagerow{left:147px;top:141px;width:683px;height:20px;background:var(--grey-panel);font-size:10.5px;display:flex;align-items:center}
.pagerow .count{padding-left:14px;width:252px}
.pager{height:22px;margin-top:-6px;background:var(--ink);color:#fff;border-radius:0 0 4px 4px;padding:4px 11px;font-size:11px;width:180px;text-align:center}
.pager em{color:var(--green-bright);font-style:normal}
.order{margin-left:auto;padding-right:10px}
.order .on,.band .on{color:var(--red)}
.band{left:147px;top:164px;width:683px;height:18px;background:var(--grey-band);font-size:10.5px;display:flex;align-items:center;justify-content:center;gap:22px}

.results{left:147px;width:683px}
.row{height:35.7px;border-bottom:1px solid var(--rule);display:grid;grid-template-columns:280px 130px 50px 62px 46px 60px 1fr;align-items:end;padding-bottom:5px;font-size:10px;color:var(--muted)}
.row .title{font-family:"Arimo",sans-serif;font-size:13px;color:#444}
.row .site{color:var(--red);text-align:center;font-size:10.5px;padding-bottom:2px}
.row svg{width:13px;height:13px;justify-self:center;margin-bottom:1px}
.badge{display:flex;align-items:center;gap:4px}
.badge b{width:13px;height:13px;color:#fff;font-size:9px;display:flex;align-items:center;justify-content:center}
.p b{background:var(--blue)}.s b{background:var(--seed)}

.comment{left:147px;top:689px;width:683px;height:179px;background:var(--grey-panel)}
.comment .tab{position:absolute;left:65px;top:-2px;background:var(--ink);color:#fff;font-size:13px;padding:6px 10px;border-radius:0 0 6px 6px;height:30px}
.comment .field{position:absolute;left:48px;top:40px;width:586px;height:102px;border:1px solid #555;border-radius:3px;background:linear-gradient(#e2e2e2,#fff 50%)}
.btn{position:absolute;top:150px;height:21px;border:1px solid #666;border-radius:3px;background:linear-gradient(#fff,#ddd);font-size:9.5px;font-weight:700;color:#444;display:flex;align-items:center;justify-content:center;gap:3px}
.btn.clear{left:498px;width:57px}.btn.submit{left:574px;width:61px}

.related-head{left:147px;top:890px;width:683px;height:21px;background:var(--grey-panel);color:var(--red);font-size:13px;padding:2px 13px}

.footer{left:147px;top:1147px;width:684px;height:53px;background:linear-gradient(var(--bar-top),var(--bar-bottom));border-radius:8px 8px 0 0;color:#fff;font-size:11px;text-align:center;padding-top:23px}
.footer a{color:var(--green-bright);text-decoration:none}

.panel{left:847px;width:138px;background:linear-gradient(#3a3a3a,#1a1a1a);border-radius:6px 0 0 6px}
.welcome{top:78px;height:144px;text-align:center;padding-top:6px}
.welcome .hi{color:var(--green-bright);font-size:9px}
.avatar{width:77px;height:76px;margin:5px auto 0;background:linear-gradient(#e8e8e8,#bdbdbd);border:1px solid #fff}
.welcome .status{color:var(--green-bright);font-size:11.5px;margin-top:6px}
.welcome .edit{width:38px;margin:2px auto 0;background:linear-gradient(#fff,#ccc);font-size:9px;color:#222;border-radius:2px;padding:1px 0}
.members{top:268px;height:246px;padding:10px 0 0 15px}
.members h2{color:var(--green-bright);font-weight:400;font-size:14px;margin-bottom:4px}
.members li{list-style:none;color:#fff;font-size:12.5px;line-height:14.3px;display:flex;align-items:center;gap:6px;padding-left:10px}
.members li svg{width:10px;height:11px}
</style>
</head>
<body>
<svg width="0" height="0" style="position:absolute">
  <symbol id="ico-plus" viewBox="0 0 14 14"><circle cx="7" cy="7" r="5.6" fill="none" stroke="#2dab3c" stroke-width="1.8"/><path d="M7 4v6M4 7h6" stroke="#2dab3c" stroke-width="1.8"/></symbol>
  <symbol id="ico-minus" viewBox="0 0 14 14"><circle cx="7" cy="7" r="5.6" fill="none" stroke="#d0202a" stroke-width="1.8"/><path d="M4 7h6" stroke="#d0202a" stroke-width="1.8"/></symbol>
  <symbol id="ico-mid" viewBox="0 0 14 14"><circle cx="7" cy="7" r="5.6" fill="none" stroke="#f08a1c" stroke-width="1.8"/><circle cx="7" cy="7" r="3.2" fill="#f08a1c"/></symbol>
  <symbol id="ico-user" viewBox="0 0 10 11"><circle cx="5" cy="3" r="2.6" fill="#2dab3c"/><path d="M0 11c0-4 2-5.5 5-5.5s5 1.5 5 5.5z" fill="#2dab3c"/></symbol>
</svg>

<div class="abs social left"><span class="s1"></span><span class="s2"></span><span class="s3"></span><span class="s4"></span></div>
<div class="abs social right"><span class="s5"></span><span class="s6"></span><span class="s7"></span><span class="s8"></span></div>

<div class="abs brand">
  <div class="brand-name"><i></i>Qentrova</div>
  <div class="brand-tag">TORRENTS SEARCH ENGINE</div>
</div>

<nav class="abs topnav">
  <a class="active" href="#">HOME</a><span class="sep">|</span><a href="#">ABOUT US</a><span class="sep">|</span><a href="#">TORRENT SEARCH</a><span class="sep">|</span><a href="#">SITE SEARCH</a><span class="sep">|</span><a href="#">HELP</a><span class="sep">|</span><a href="#">JOHN</a><span class="sep">|</span><a href="#">SIGNOUT</a>
  <div class="lang">English</div>
</nav>

<div class="abs searchbar"><div class="query">starforgers 3</div><div class="go"><svg width="9" height="9" viewBox="0 0 10 10"><circle cx="4" cy="4" r="3" fill="none" stroke="#fff" stroke-width="1.5"/><path d="M6 6l3.5 3.5" stroke="#fff" stroke-width="1.5"/></svg>SEARCH</div></div>
<div class="abs stats">About 50,000 results (0.12 seconds)</div>
<div class="abs include">Sites search include <b></b></div>

<div class="abs pagerow">
  <div class="count">1 - 10 of 20 for “ starforgers 3 ” ( 1,155s )</div>
  <div class="pager">previous | 1 | 2 | <em>3</em> | 4 | next</div>
  <div class="order">Order by : | <span class="on">name</span> | date | size | peers | seeds</div>
</div>
<div class="abs band"><span>Quality : | <span class="on">all</span> | good | bad | verified</span><span>Search by : | filename | <span class="on">titles</span> | data added</span></div>

<div class="abs results" style="top:203px">
  <div class="row"><span class="title">starforgers 3 HD XVD bgfsbsb.225</span><span class="site">seedharbor.com</span><svg><use href="#ico-plus"/></svg><span>3 days ago</span><span>549 MB</span><span class="badge p"><b>P</b>10.555</span><span class="badge s"><b>S</b>10.200</span></div>
  <div class="row"><span class="title">starforgers 3 HD XVD bgfsbsb.225</span><span class="site">kavelo.eu</span><svg><use href="#ico-minus"/></svg><span>3 days ago</span><span>549 MB</span><span class="badge p"><b>P</b>10.555</span><span class="badge s"><b>S</b>10.200</span></div>
  <div class="row"><span class="title">starforgers 3 HD XVD bgfsbsb.225</span><span class="site">yourpeerfiles.com</span><svg><use href="#ico-plus"/></svg><span>3 days ago</span><span>549 MB</span><span class="badge p"><b>P</b>10.555</span><span class="badge s"><b>S</b>10.200</span></div>
  <div class="row"><span class="title">starforgers 3 HD XVD bgfsbsb.225</span><span class="site">torrentgrove.com</span><svg><use href="#ico-plus"/></svg><span>3 days ago</span><span>549 MB</span><span class="badge p"><b>P</b>10.555</span><span class="badge s"><b>S</b>10.200</span></div>
  <div class="row"><span class="title">starforgers 3 HD XVD bgfsbsb.225</span><span class="site">bitmeadow.com</span><svg><use href="#ico-minus"/></svg><span>3 days ago</span><span>549 MB</span><span class="badge p"><b>P</b>10.555</span><span class="badge s"><b>S</b>10.200</span></div>
  <div class="row"><span class="title">starforgers 3 HD XVD bgfsbsb.225</span><span class="site">seedharbor.com</span><svg><use href="#ico-mid"/></svg><span>3 days ago</span><span>549 MB</span><span class="badge p"><b>P</b>10.555</span><span class="badge s"><b>S</b>10.200</span></div>
  <div class="row"><span class="title">starforgers 3 HD XVD bgfsbsb.225</span><span class="site">kavelo.eu</span><svg><use href="#ico-plus"/></svg><span>3 days ago</span><span>549 MB</span><span class="badge p"><b>P</b>10.555</span><span class="badge s"><b>S</b>10.200</span></div>
  <div class="row"><span class="title">starforgers 3 HD XVD bgfsbsb.225</span><span class="site">yourpeerfiles.com</span><svg><use href="#ico-plus"/></svg><span>3 days ago</span><span>549 MB</span><span class="badge p"><b>P</b>10.555</span><span class="badge s"><b>S</b>10.200</span></div>
  <div class="row"><span class="title">starforgers 3 HD XVD bgfsbsb.225</span><span class="site">torrentgrove.com</span><svg><use href="#ico-mid"/></svg><span>3 days ago</span><span>549 MB</span><span class="badge p"><b>P</b>10.555</span><span class="badge s"><b>S</b>10.200</span></div>
  <div class="row"><span class="title">starforgers 3 HD XVD bgfsbsb.225</span><span class="site">bitmeadow.com</span><svg><use href="#ico-minus"/></svg><span>3 days ago</span><span>549 MB</span><span class="badge p"><b>P</b>10.555</span><span class="badge s"><b>S</b>10.200</span></div>
  <div class="row"><span class="title">starforgers 3 HD XVD bgfsbsb.225</span><span class="site">seedharbor.com</span><svg><use href="#ico-mid"/></svg><span>3 days ago</span><span>549 MB</span><span class="badge p"><b>P</b>10.555</span><span class="badge s"><b>S</b>10.200</span></div>
  <div class="row"><span class="title">starforgers 3 HD XVD bgfsbsb.225</span><span class="site">kavelo.eu</span><svg><use href="#ico-plus"/></svg><span>3 days ago</span><span>549 MB</span><span class="badge p"><b>P</b>10.555</span><span class="badge s"><b>S</b>10.200</span></div>
  <div class="row"><span class="title">starforgers 3 HD XVD bgfsbsb.225</span><span class="site">yourpeerfiles.com</span><svg><use href="#ico-plus"/></svg><span>3 days ago</span><span>549 MB</span><span class="badge p"><b>P</b>10.555</span><span class="badge s"><b>S</b>10.200</span></div>
</div>

<section class="abs comment">
  <div class="tab">POST A COMMENT</div>
  <div class="field"></div>
  <div class="btn clear"><svg width="8" height="9" viewBox="0 0 8 9"><path d="M1 2h6M2 2l.5 6.5h3L6 2M3 2V1h2v1" fill="none" stroke="#444"/></svg>CLEAR</div>
  <div class="btn submit"><svg width="8" height="9" viewBox="0 0 8 9"><path d="M4 0L0 4.5h2.5V9h3V4.5H8z" fill="#444"/></svg>SUBMIT</div>
</section>

<div class="abs related-head">starforgers 3 &nbsp;related torrents</div>
<div class="abs results" style="top:911px">
  <div class="row"><span class="title">starforgers 3 HD XVD bgfsbsb.225</span><span class="site">seedharbor.com</span><svg><use href="#ico-plus"/></svg><span>3 days ago</span><span>549 MB</span><span class="badge p"><b>P</b>10.555</span><span class="badge s"><b>S</b>10.200</span></div>
  <div class="row"><span class="title">starforgers 3 HD XVD bgfsbsb.225</span><span class="site">kavelo.eu</span><svg><use href="#ico-minus"/></svg><span>3 days ago</span><span>549 MB</span><span class="badge p"><b>P</b>10.555</span><span class="badge s"><b>S</b>10.200</span></div>
  <div class="row"><span class="title">starforgers 3 HD XVD bgfsbsb.225</span><span class="site">yourpeerfiles.com</span><svg><use href="#ico-plus"/></svg><span>3 days ago</span><span>549 MB</span><span class="badge p"><b>P</b>10.555</span><span class="badge s"><b>S</b>10.200</span></div>
  <div class="row"><span class="title">starforgers 3 HD XVD bgfsbsb.225</span><span class="site">torrentgrove.com</span><svg><use href="#ico-plus"/></svg><span>3 days ago</span><span>549 MB</span><span class="badge p"><b>P</b>10.555</span><span class="badge s"><b>S</b>10.200</span></div>
  <div class="row"><span class="title">starforgers 3 HD XVD bgfsbsb.225</span><span class="site">bitmeadow.com</span><svg><use href="#ico-minus"/></svg><span>3 days ago</span><span>549 MB</span><span class="badge p"><b>P</b>10.555</span><span class="badge s"><b>S</b>10.200</span></div>
  <div class="row"><span class="title">starforgers 3 HD XVD bgfsbsb.225</span><span class="site">seedharbor.com</span><svg><use href="#ico-mid"/></svg><span>3 days ago</span><span>549 MB</span><span class="badge p"><b>P</b>10.555</span><span class="badge s"><b>S</b>10.200</span></div>
</div>

<footer class="abs footer">COPYRIGHT © 2011 QENTROVA. USE OF THIS WEBSITE CONSTITUTES ACCEPTANCE OF OUR <a href="#">USER AGREEMENT</a> AND <a href="#">PRIVACY POLICY</a>.</footer>

<aside class="abs panel welcome">
  <div class="hi">WELCOME JOHN</div>
  <div class="avatar" role="img" aria-label="Member profile picture"></div>
  <div class="status">PROFILE STATUS</div>
  <div class="edit">EDIT</div>
</aside>
<aside class="abs panel members">
  <h2>OTHER MEMBERS</h2>
  <ul>
    <li><svg><use href="#ico-user"/></svg>MAILO</li>
    <li><svg><use href="#ico-user"/></svg>HASKE</li>
    <li><svg><use href="#ico-user"/></svg>VISUAL 25</li>
    <li><svg><use href="#ico-user"/></svg>DEAD FORCE</li>
    <li><svg><use href="#ico-user"/></svg>JACY</li>
    <li><svg><use href="#ico-user"/></svg>JESICA 23</li>
    <li><svg><use href="#ico-user"/></svg>MATT 19</li>
    <li><svg><use href="#ico-user"/></svg>MAILO</li>
    <li><svg><use href="#ico-user"/></svg>HASKE</li>
    <li><svg><use href="#ico-user"/></svg>VISUAL 25</li>
    <li><svg><use href="#ico-user"/></svg>DEAD FORCE</li>
    <li><svg><use href="#ico-user"/></svg>JACY</li>
    <li><svg><use href="#ico-user"/></svg>JESICA 23</li>
    <li><svg><use href="#ico-user"/></svg>MATT 19</li>
  </ul>
</aside>
</body>
</html>
```